Web Design For Marlow Pool Service

We are working with a company that wants a website for their pool service. Some sites to use for content/competitors and inspiration:
https://sacramento.brightwaterpoolco.example/builder/newbuild/repair/ppc
https://hollowbrookpoolcareplus.example/
https://lakemontpoolservice.example/
https://www.dravenspoolresurfacing.example/pool-renovation-ga/
Thank you for taking the time to consider designing a website for us. We are web developers based in Stockton, CA, USA. Most of our projects go through the same process. Understanding this process may help you win a project with us. We custom-code all of our websites in-house. We don’t have any requirements as to what tools you use for your design, but we prefer Figma files. For any design that we label as four-stars, we send it to the client for review. The client picks the final design they want us to use. Once we complete this process, we will continue to show additional clients all the four-star sites and purchase them later. Your designs will have multiple chances to sell. For better chances of success, we ask that you follow these guidelines.
IMAGES:
If you use any images or icons in the design, we ask that you have a link to the asset so we can purchase the image/icon. Most of the designs we submit do not have the customer’s images on them unless they have some great images. Be creative; show us the feeling you are trying to portray with your image choices. Use any royalty-free site you choose. We subscribe to Adobe and mainly use their images, but we can purchase images outside of Adobe. PLEASE NOTE: we will not submit designs to clients with watermarks on the images.
FONTS:
We ask that you identify the fonts used in the design. This can be done in a message if you want. We typically use Google Fonts and Adobe Fonts.
CONTENT:
We're always open to different content and ideas. We often submit designs with stock images so the client can see our vision. We typically take pictures after the website launch to use their images with our vision. Lorem Ipsum is fine for paragraphs, but we ask that you write the headers in correct English. We want to be able to show the vision and identify the sections of the website.
INSPIRATION:
We typically add a couple of links in the brief of websites we like to help you get started in your design.
REVISIONS:
We do not often ask for revisions of the designs unless we see something in the design that may not appeal to the client. If there are slight changes that we want to make, we do that in the development process.
FEEDBACK:
We rarely give feedback on designs during the design process. We are working on many website projects and do not have the time to provide feedback. We usually respond if your request is well thought out and asks specific questions, but a note asking “feedback, please” usually goes unanswered.
Number of Pages Required
1 page
Look and feel
Each slider illustrates characteristics of the customer's brand and the style your logo design should communicate.

```html
<!DOCTYPE html>
<html lang="en">
<head>
<meta charset="utf-8">
<title>Marlow Pool Service</title>
<link rel="stylesheet" href="https://fonts.googleapis.com/css2?family=Open+Sans:wght@400;500;600;700;800&family=Poppins:wght@500;600&display=swap">
<style>
:root{
  --navy:#0f2a4f;
  --navy-dark:#1e2838;
  --heading:#1a3d6d;
  --blue:#2196f3;
  --blue-deep:#1b4f91;
  --text:#6b7280;
  --ink:#1f2937;
  --light:#f4f4f4;
  --line:#e5e7eb;
  --white:#ffffff;
}
*{box-sizing:border-box;margin:0;padding:0}
html,body{width:1200px;height:4841px;overflow:hidden}
body{position:relative;font-family:"Open Sans",sans-serif;color:var(--ink);background:var(--white)}
.abs{position:absolute}
.label{font-size:12px;letter-spacing:.3px;color:var(--blue);text-transform:uppercase;text-decoration:underline;text-underline-offset:3px}
.h2{font-weight:700;color:var(--heading);font-size:42px;line-height:1.2}
.para{font-size:13px;line-height:22px;color:var(--text)}
.btn{display:flex;align-items:center;justify-content:center;gap:14px;background:var(--blue);color:#fff;font-weight:600;font-size:15px;border-radius:3px}
.logo{font-family:"Poppins",sans-serif;font-weight:600;display:flex;align-items:center;gap:10px}
.logo .dot{width:18px;height:18px;border-radius:50%;background:currentColor;display:inline-block}

/* top bar */
.topbar{left:0;top:0;width:1200px;height:46px;background:var(--navy-dark);color:#d1d5db;font-size:14px}
.topbar .item{top:14px;display:flex;align-items:center;gap:8px}
.topbar .social{top:17px;width:11px;height:11px;border-radius:2px;background:#aeb6c2}

/* header */
.header{left:0;top:46px;width:1200px;height:110px;background:#fff}
.header .logo{left:104px;top:36px;font-size:22px;color:var(--blue-deep)}
.info{display:flex;gap:16px;align-items:center;top:30px}
.info .t1{font-size:14px;color:var(--ink)}
.info .t2{font-size:13px;color:var(--text);margin-top:3px}
.estimate{left:958px;top:30px;width:180px;height:48px;background:var(--blue-deep);color:#fff;font-size:14px;font-weight:700;border-radius:4px}

/* hero */
.hero{left:0;top:156px;width:1200px;height:810px;background:linear-gradient(100deg,#2d4a52 0%,#47666a 30%,#7a6d5e 55%,#586a5f 75%,#2f4a44 100%)}
.hero-shade{left:0;top:156px;width:1200px;height:810px;background:linear-gradient(90deg,rgba(10,25,40,.55),rgba(10,25,40,.1) 70%)}
.nav{left:79px;top:156px;width:1057px;height:66px;background:#fff;font-size:14px;color:var(--text)}
.nav a{position:absolute;top:24px;text-decoration:none;color:var(--text)}
.nav a.active{color:var(--blue-deep);font-weight:600}
.nav .call{position:absolute;left:986px;top:0;width:71px;height:66px;background:var(--navy);display:flex;align-items:center;justify-content:center}
.welcome{left:100px;top:451px;width:266px;height:41px;background:var(--blue-deep);border-left:4px solid var(--blue);color:#fff;font-weight:700;font-size:20px;padding:8px 20px}
.hero-title{left:100px;top:518px;font-size:60px;font-weight:800;color:#fff;letter-spacing:.5px;white-space:nowrap}
.hero-text{left:100px;top:608px;width:440px;font-size:16px;line-height:27px;color:#f3f4f6}
.hero-btn{left:100px;top:689px;width:176px;height:53px;font-size:15px}

/* about */
.about-title{left:94px;top:1096px}
.about-sub{left:94px;top:1222px;font-size:21px;font-weight:500;color:var(--ink)}
.img-a{left:618px;top:1044px;width:233px;height:423px;background:linear-gradient(160deg,#4fc3e8,#2aa7d6 45%,#e77aa0 60%,#30a9d8)}
.img-b{left:870px;top:1072px;width:234px;height:428px;background:linear-gradient(160deg,#c8ccd0,#8a9097 40%,#c0392b 60%,#6b7280);border:1px solid #ddd}
.badge{left:818px;top:1231px;width:80px;height:80px;border-radius:50%;background:var(--navy);border:4px solid #fff}

/* services */
.services-bg{left:0;top:1560px;width:1200px;height:647px;background:var(--light)}
.more{left:943px;top:1666px;font-size:14px;color:var(--ink)}
.more-box{left:1076px;top:1658px;width:40px;height:40px;background:var(--blue);display:flex;align-items:center;justify-content:center}
.svc{top:1767px;width:318px;height:353px;border-radius:4px;overflow:hidden}
.svc .shade{position:absolute;inset:0;background:linear-gradient(180deg,rgba(0,0,0,0) 40%,rgba(0,0,0,.75))}
.svc .dot{position:absolute;left:22px;top:232px;width:22px;height:22px;border-radius:50%;background:var(--blue)}
.svc .title{position:absolute;left:30px;top:232px;font-size:24px;font-weight:700;color:#fff}
.svc .arrow{position:absolute;left:28px;top:282px;width:48px;height:48px;border-radius:50%;background:rgba(255,255,255,.2);display:flex;align-items:center;justify-content:center}

/* experts */
.experts-bg{left:0;top:2207px;width:1200px;height:385px;background:linear-gradient(110deg,#15273f,#23405e 45%,#1a3047 70%,#2b3f3a)}
.experts-title{left:90px;top:2312px;font-size:40px;font-weight:700;color:#fff;line-height:53px}
.experts-btn{left:92px;top:2485px;width:156px;height:47px}
.feature{top:2319px;width:232px;height:361px;background:#fff;box-shadow:0 6px 20px rgba(0,0,0,.08);text-align:center;padding-top:44px}
.feature .t{font-size:20px;font-weight:700;color:var(--blue-deep);margin-top:14px}
.feature p{font-size:14px;line-height:25px;color:var(--text);margin:12px auto 0;width:170px}
.feature .more-link{font-size:13px;font-weight:700;color:var(--ink);margin-top:34px;display:flex;gap:8px;justify-content:center;align-items:center}

/* why */
.center-label{width:1200px;text-align:center}
.portrait{left:434px;top:2907px;width:326px;height:326px;border-radius:50%;background:radial-gradient(circle at 50% 40%,#8c99a8,#4b5563 55%,#1f2937)}
.ring{width:80px;height:80px;border-radius:50%;background:#fff;box-shadow:0 4px 16px rgba(0,0,0,.09);display:flex;align-items:center;justify-content:center}
.why-item .t{font-size:20px;font-weight:500;color:var(--blue-deep)}
.why-item p{font-size:13px;line-height:21px;color:var(--text);margin-top:4px;width:210px}

/* testimonials */
.testi-bg{left:0;top:3333px;width:1200px;height:535px;background:var(--navy)}
.quote{top:3547px;width:321px;height:214px;background:#1d3a63;border-radius:3px;padding:0 32px}
.quote .mark{display:block;margin:-8px auto 0}
.quote p{font-size:13px;line-height:23px;color:#e5e7eb;margin-top:10px}
.quote .who{display:flex;align-items:center;gap:12px;margin-top:14px}
.quote .av{width:48px;height:48px;border-radius:50%;background:linear-gradient(135deg,#b9c2cc,#6b7280)}
.quote .n{font-size:16px;font-weight:600;color:#fff}
.quote .c{font-size:15px;color:#8ea0b8}
.dots{left:566px;top:3789px;display:flex;gap:8px;align-items:center}
.dots i{width:6px;height:6px;border-radius:50%;background:#9fb0c8;display:block}

/* contact */
.contact-title{left:107px;top:3976px;font-size:40px;font-weight:700;color:var(--heading)}
.contact-title span{font-weight:400}
.c-item{left:112px;display:flex;gap:30px}
.c-item .ic{width:40px;height:40px;border-radius:50%;background:#eef3f8;display:flex;align-items:center;justify-content:center}
.c-item .k{font-size:13px;font-weight:700;color:var(--ink)}
.c-item .v{font-size:13px;color:var(--text);margin-top:4px}
.form{left:601px;top:3978px;width:494px;height:569px;background:#fff;border-top:5px solid var(--blue-deep);box-shadow:0 10px 40px rgba(0,0,0,.08);padding:38px 38px}
.form h3{font-size:25px;font-weight:600;color:var(--ink)}
.form .lab{position:absolute;font-size:13px;font-weight:700;color:var(--ink)}
.form .field{position:absolute;height:45px;border:1px solid #cfd4da;border-radius:24px;font-size:13px;color:#9ca3af;padding:13px 24px}
.form .area{border-radius:3px;height:124px}
.form .btn{position:absolute;left:39px;top:469px;width:155px;height:45px}

/* footer */
.f-logo{left:154px;top:4612px;font-size:24px;color:#fff}
.f-info{top:4620px;display:flex;gap:14px;align-items:center;color:#fff;font-size:13px;line-height:18px}
.f-div{top:4610px;width:1px;height:52px;background:rgba(255,255,255,.25)}
.f-nav{left:257px;top:4695px;width:697px;height:57px;border-top:1px solid rgba(255,255,255,.25);border-bottom:1px solid rgba(255,255,255,.25);display:flex;justify-content:space-around;align-items:center;color:#fff;font-size:14px}
.f-copy{left:146px;top:4793px;font-size:12px;color:#d1d5db}
.f-social{top:4789px;width:25px;height:25px;border:1px solid rgba(255,255,255,.6);display:flex;align-items:center;justify-content:center}
.f-social i{width:10px;height:10px;background:#fff;border-radius:2px;display:block}
</style>
</head>
<body>

<!-- top bar -->
<div class="abs topbar">
  <div class="abs item" style="left:78px">
    <svg width="14" height="14" viewBox="0 0 16 16"><circle cx="8" cy="8" r="6.5" fill="none" stroke="#2196f3" stroke-width="1.5"/><path d="M8 4v4l3 2" stroke="#2196f3" stroke-width="1.5" fill="none"/></svg>
    Mon-Sat: 09am to 07:30pm
  </div>
  <div class="abs item" style="left:325px">
    <svg width="15" height="12" viewBox="0 0 16 12"><rect x="1" y="1" width="14" height="10" rx="1.5" fill="none" stroke="#2196f3" stroke-width="1.4"/><path d="M1 2l7 5 7-5" stroke="#2196f3" stroke-width="1.4" fill="none"/></svg>
    needhelp@lorem.com
  </div>
  <div class="abs" style="left:862px;top:10px;width:1px;height:26px;background:#4b5563"></div>
  <div class="abs item" style="left:887px">Faqs</div>
  <div class="abs item" style="left:953px">Pricing</div>
  <div class="abs" style="left:1020px;top:10px;width:1px;height:26px;background:#4b5563"></div>
  <span class="abs social" style="left:1037px"></span>
  <span class="abs social" style="left:1063px"></span>
  <span class="abs social" style="left:1094px"></span>
  <span class="abs social" style="left:1124px"></span>
</div>

<!-- header -->
<div class="abs header">
  <div class="abs logo"><span class="dot"></span>Marlow Pool Service</div>
  <div class="abs info" style="left:362px">
    <svg width="36" height="34" viewBox="0 0 36 34"><path d="M4 12c0-5 6-8 14-8s14 3 14 8l-1 4h-6l-1-4H12l-1 4H5z" fill="none" stroke="#1b4f91" stroke-width="2"/><rect x="8" y="18" width="20" height="13" rx="2" fill="none" stroke="#1b4f91" stroke-width="2"/><circle cx="18" cy="24.5" r="3" fill="none" stroke="#1b4f91" stroke-width="2"/></svg>
    <div><div class="t1">+12-345-67-8900</div><div class="t2">Need help? Make a Call</div></div>
  </div>
  <div class="abs info" style="left:664px">
    <svg width="34" height="34" viewBox="0 0 34 34"><circle cx="17" cy="17" r="14" fill="none" stroke="#1b4f91" stroke-width="2"/><path d="M3 17h28M17 3c-6 8-6 20 0 28M17 3c6 8 6 20 0 28" fill="none" stroke="#1b4f91" stroke-width="2"/></svg>
    <div><div class="t1">USA</div><div class="t2">212A Someplace somewhere</div></div>
  </div>
  <div class="abs btn estimate">Free Estimate
    <svg width="20" height="20" viewBox="0 0 20 20"><circle cx="10" cy="10" r="8.5" fill="none" stroke="#fff" stroke-width="1.5"/><path d="M6 10h8M11 7l3 3-3 3" stroke="#fff" stroke-width="1.5" fill="none"/></svg>
  </div>
</div>

<!-- hero -->
<div class="abs hero" role="img" aria-label="Photo of a woman relaxing at the edge of a pool"></div>
<div class="abs hero-shade"></div>
<svg class="abs" style="left:0;top:156px" width="1200" height="810" viewBox="0 0 1200 810">
  <path d="M0 792 C 420 752, 880 700, 1200 652 L1200 810 L0 810Z" fill="#fff"/>
  <path d="M0 764 C 230 768, 480 748, 690 740 C 470 775, 230 792, 0 800Z" fill="#2196f3"/>
</svg>
<nav class="abs nav">
  <a class="active" style="left:86px">Home</a>
  <a style="left:198px">About Us</a>
  <a style="left:310px">Services</a>
  <a style="left:423px">Gallery</a>
  <a style="left:542px">Our Team</a>
  <a style="left:692px">Contact Us</a>
  <div class="call">
    <svg width="36" height="36" viewBox="0 0 24 24"><path d="M5 3h4l2 5-2.5 1.5a11 11 0 0 0 6 6L16 13l5 2v4a2 2 0 0 1-2 2A16 16 0 0 1 3 5a2 2 0 0 1 2-2z" fill="none" stroke="#fff" stroke-width="1.4"/></svg>
  </div>
</nav>
<div class="abs welcome">Welcome</div>
<h1 class="abs hero-title">Dive into Your Dream Pool</h1>
<p class="abs hero-text">Lorem ipsum dolor sit amet, consectetur adipiscing elit, sed do eiusmod tempor i</p>
<div class="abs btn hero-btn">Read More</div>

<!-- about -->
<div class="abs label" style="left:94px;top:1062px">Who we are</div>
<h2 class="abs h2 about-title">Crafting Aquatic<br>Masterpieces</h2>
<div class="abs about-sub">Making Waves with Excellence</div>
<p class="abs para" style="left:94px;top:1271px;width:505px">Lorem ipsum dolor sit amet, consectetur adipiscing elit, sed do eiusmod temp or incididunt ut labore et dolore magna aliqua. Ut enim ad minim veniam, quis laboris nisi ut aliquip ex ea commodo consequat.</p>
<p class="abs para" style="left:94px;top:1347px;width:505px">Lorem ipsum dolor sit amet, consectetur adipiscing elit, sed do eiusmod temp or incididunt ut labore et dolore magna aliqua.</p>
<div class="abs btn" style="left:92px;top:1427px;width:154px;height:47px">Contact us
  <svg width="18" height="14" viewBox="0 0 18 14"><path d="M1 7h15M11 2l5 5-5 5" stroke="#fff" stroke-width="1.6" fill="none"/></svg>
</div>
<div class="abs img-a" role="img" aria-label="Aerial photo of a woman floating on an inflatable in a pool"></div>
<div class="abs img-b" role="img" aria-label="Photo of a technician repairing pool equipment"></div>
<div class="abs badge"></div>

<!-- services -->
<div class="abs services-bg"></div>
<div class="abs label" style="left:90px;top:1619px">Our services</div>
<h2 class="abs h2" style="left:86px;top:1651px">Services We Provide</h2>
<div class="abs more">More Services</div>
<div class="abs more-box"><svg width="12" height="14" viewBox="0 0 12 14"><path d="M3 2l6 5-6 5" stroke="#fff" stroke-width="2" fill="none"/></svg></div>

<div class="abs svc" style="left:98px;background:linear-gradient(150deg,#6aa5c4,#3c6f8f 45%,#3a3a34)" role="img" aria-label="Photo of a worker repairing pool tiles">
  <div class="shade"></div><span class="dot"></span><div class="title">Pool Repair</div>
  <div class="arrow"><svg width="16" height="14" viewBox="0 0 16 14"><path d="M1 7h13M9 2l5 5-5 5" stroke="#fff" stroke-width="1.5" fill="none"/></svg></div>
</div>
<div class="abs svc" style="left:443px;background:linear-gradient(150deg,#b8b9b4,#8d8a7c 45%,#3f4a2c)" role="img" aria-label="Photo of a construction worker in a hard hat">
  <div class="shade"></div><span class="dot"></span><div class="title">Pool Construction</div>
  <div class="arrow"><svg width="16" height="14" viewBox="0 0 16 14"><path d="M1 7h13M9 2l5 5-5 5" stroke="#fff" stroke-width="1.5" fill="none"/></svg></div>
</div>
<div class="abs svc" style="left:789px;background:linear-gradient(150deg,#9db08a,#5f8a8a 45%,#2a4f5a)" role="img" aria-label="Photo of a family enjoying a clean pool">
  <div class="shade"></div><span class="dot"></span><div class="title">Pool Cleaning</div>
  <div class="arrow"><svg width="16" height="14" viewBox="0 0 16 14"><path d="M1 7h13M9 2l5 5-5 5" stroke="#fff" stroke-width="1.5" fill="none"/></svg></div>
</div>

<!-- experts -->
<div class="abs experts-bg" role="img" aria-label="Dark photo of a pool with surrounding trees at dusk"></div>
<h2 class="abs experts-title">Leading<br>Experts</h2>
<div class="abs btn experts-btn">Contact us
  <svg width="18" height="14" viewBox="0 0 18 14"><path d="M1 7h15M11 2l5 5-5 5" stroke="#fff" stroke-width="1.6" fill="none"/></svg>
</div>
<div class="abs feature" style="left:355px">
  <svg width="42" height="42" viewBox="0 0 24 24"><circle cx="12" cy="12" r="3.2" fill="none" stroke="#1b4f91" stroke-width="1.3"/><path d="M12 2.5l2 2.2 3-.6.6 3 2.7 1.4-1.3 2.8 1.3 2.8-2.7 1.4-.6 3-3-.6-2 2.2-2-2.2-3 .6-.6-3L3.7 14.3 5 11.5 3.7 8.7l2.7-1.4.6-3 3 .6z" fill="none" stroke="#1b4f91" stroke-width="1.3"/></svg>
  <div class="t">Expertise</div>
  <p>Lorem ipsum dolor sit consectetur adipiscing elit, sed do eiusmod tempor incididunt</p>
  <div class="more-link">Read More <svg width="12" height="10" viewBox="0 0 12 10"><path d="M1 5h9M7 2l3 3-3 3" stroke="#1f2937" stroke-width="1.4" fill="none"/></svg></div>
</div>
<div class="abs feature" style="left:614px">
  <svg width="42" height="42" viewBox="0 0 24 24"><circle cx="11" cy="11" r="7.5" fill="none" stroke="#1b4f91" stroke-width="1.3"/><circle cx="16" cy="16" r="4" fill="#fff" stroke="#1b4f91" stroke-width="1.3"/><path d="M14.5 16l1 1 2-2" stroke="#1b4f91" stroke-width="1.3" fill="none"/><path d="M7 10h6M7 7h4" stroke="#1b4f91" stroke-width="1.3"/></svg>
  <div class="t">Professional</div>
  <p>Lorem ipsum dolor sit consectetur adipiscing elit, sed do eiusmod tempor incididunt</p>
  <div class="more-link">Read More <svg width="12" height="10" viewBox="0 0 12 10"><path d="M1 5h9M7 2l3 3-3 3" stroke="#1f2937" stroke-width="1.4" fill="none"/></svg></div>
</div>
<div class="abs feature" style="left:875px">
  <svg width="42" height="42" viewBox="0 0 24 24"><circle cx="12" cy="7.5" r="4.5" fill="none" stroke="#1b4f91" stroke-width="1.3"/><path d="M3.5 21.5v-2a5 5 0 0 1 5-5h7a5 5 0 0 1 5 5v2z" fill="none" stroke="#1b4f91" stroke-width="1.3"/></svg>
  <div class="t">Experienced</div>
  <p>Lorem ipsum dolor sit consectetur adipiscing elit, sed do eiusmod tempor incididunt</p>
  <div class="more-link">Read More <svg width="12" height="10" viewBox="0 0 12 10"><path d="M1 5h9M7 2l3 3-3 3" stroke="#1f2937" stroke-width="1.4" fill="none"/></svg></div>
</div>

<!-- why choose us -->
<div class="abs center-label" style="left:0;top:2740px"><span class="label">Our services</span></div>
<h2 class="abs h2 center-label" style="left:0;top:2776px">Why Choose Us</h2>
<svg class="abs" style="left:0;top:2880px" width="1200" height="380" viewBox="0 0 1200 380">
  <path d="M392 65 C 340 100, 340 220, 392 314" fill="none" stroke="#9ca3af" stroke-width="1.2"/>
  <path d="M806 65 C 860 100, 860 220, 802 314" fill="none" stroke="#9ca3af" stroke-width="1.2"/>
</svg>
<div class="abs portrait" role="img" aria-label="Portrait photo of a smiling team member in a grey suit"></div>

<div class="abs ring" style="left:352px;top:2905px"><svg width="22" height="22" viewBox="0 0 24 24"><path d="M4 14v-2a8 8 0 0 1 16 0v2M4 14h3v5H4zM17 14h3v5h-3z" fill="none" stroke="#2196f3" stroke-width="1.5"/></svg></div>
<div class="abs ring" style="left:321px;top:3030px"><svg width="22" height="22" viewBox="0 0 24 24"><path d="M12 3l2.7 5.6 6.1.8-4.4 4.3 1 6.1L12 17l-5.4 2.8 1-6.1L3.2 9.4l6.1-.8z" fill="none" stroke="#2196f3" stroke-width="1.5"/></svg></div>
<div class="abs ring" style="left:352px;top:3154px"><svg width="22" height="22" viewBox="0 0 24 24"><path d="M9 3h6M10 3v6l-5 10a1.5 1.5 0 0 0 1.3 2h11.4a1.5 1.5 0 0 0 1.3-2l-5-10V3" fill="none" stroke="#2196f3" stroke-width="1.5"/></svg></div>
<div class="abs ring" style="left:766px;top:2905px"><svg width="24" height="22" viewBox="0 0 26 24"><circle cx="13" cy="8" r="3.5" fill="none" stroke="#2196f3" stroke-width="1.5"/><circle cx="5.5" cy="10" r="2.5" fill="none" stroke="#2196f3" stroke-width="1.5"/><circle cx="20.5" cy="10" r="2.5" fill="none" stroke="#2196f3" stroke-width="1.5"/><path d="M7 19a6 6 0 0 1 12 0M1.5 18a4 4 0 0 1 5-3.5M24.5 18a4 4 0 0 0-5-3.5" fill="none" stroke="#2196f3" stroke-width="1.5"/></svg></div>
<div class="abs ring" style="left:798px;top:3030px"><svg width="22" height="22" viewBox="0 0 24 24"><path d="M3 17a9 9 0 1 1 18 0z" fill="none" stroke="#2196f3" stroke-width="1.5"/><path d="M12 15l4-5" stroke="#2196f3" stroke-width="1.5"/></svg></div>
<div class="abs ring" style="left:762px;top:3154px"><svg width="22" height="22" viewBox="0 0 24 24"><path d="M20 11a8 8 0 0 0-14.5-4M4 13a8 8 0 0 0 14.5 4M5 3v4h4M19 21v-4h-4" fill="none" stroke="#2196f3" stroke-width="1.5"/></svg></div>

<div class="abs why-item" style="left:148px;top:2910px"><div class="t">Quality Assurance</div><p>Lorem ipsum dolor sit amet, consectetur adipiscing</p></div>
<div class="abs why-item" style="left:118px;top:3035px"><div class="t" style="padding-left:30px">Proven Record</div><p>Lorem ipsum dolor sit amet, consectetur adipiscing</p></div>
<div class="abs why-item" style="left:81px;top:3158px"><div class="t">Personalized Approach</div><p style="padding-left:52px;width:262px">Lorem ipsum dolor sit amet, consectetur adipiscing</p></div>
<div class="abs why-item" style="left:876px;top:2900px"><div class="t">Empathetic Staff</div><p>Lorem ipsum dolor sit amet, consectetur adipiscing</p></div>
<div class="abs why-item" style="left:900px;top:3035px"><div class="t">Professionalism</div><p>Lorem ipsum dolor sit amet, consectetur adipiscing</p></div>
<div class="abs why-item" style="left:876px;top:3160px"><div class="t">Experience and Expertise</div><p>Lorem ipsum dolor sit amet, consectetur adipiscing</p></div>

<!-- testimonials -->
<div class="abs testi-bg"></div>
<div class="abs center-label" style="left:0;top:3388px"><span class="label">Testimonials</span></div>
<h2 class="abs h2 center-label" style="left:0;top:3422px;color:#fff">What Clients are Saying</h2>

<div class="abs quote" style="left:92px">
  <svg class="mark" width="38" height="28" viewBox="0 0 38 28"><path d="M2 2h14v12l-6 12H4l5-12H2zM21 2h14v12l-6 12h-6l5-12h-7z" fill="#2196f3"/></svg>
  <p>Lorem ipsum dolor sit amet, consectetur adipiscing elit, sed do eiusmod tempor i ncididunt ut labore et dolore magna aliq ua. Ut enim ad minim veniam, quis nostr</p>
  <div class="who"><span class="av" role="img" aria-label="Client photo"></span><div><div class="n">Dana R.</div><div class="c">Country</div></div></div>
</div>
<div class="abs quote" style="left:439px">
  <svg class="mark" width="38" height="28" viewBox="0 0 38 28"><path d="M2 2h14v12l-6 12H4l5-12H2zM21 2h14v12l-6 12h-6l5-12h-7z" fill="#2196f3"/></svg>
  <p>Lorem ipsum dolor sit amet, consectetur adipiscing elit, sed do eiusmod tempor i ncididunt ut labore et dolore magna aliq ua. Ut enim ad minim veniam, quis nostr</p>
  <div class="who"><span class="av" role="img" aria-label="Client photo"></span><div><div class="n">Dana R.</div><div class="c">Country</div></div></div>
</div>
<div class="abs quote" style="left:785px">
  <svg class="mark" width="38" height="28" viewBox="0 0 38 28"><path d="M2 2h14v12l-6 12H4l5-12H2zM21 2h14v12l-6 12h-6l5-12h-7z" fill="#2196f3"/></svg>
  <p>Lorem ipsum dolor sit amet, consectetur adipiscing elit, sed do eiusmod tempor i ncididunt ut labore et dolore magna aliq ua. Ut enim ad minim veniam, quis nostr</p>
  <div class="who"><span class="av" role="img" aria-label="Client photo"></span><div><div class="n">Dana R.</div><div class="c">Country</div></div></div>
</div>
<div class="abs dots"><i></i><i></i><i style="width:10px;height:10px;background:none;border:2px solid #9fb0c8"></i><i></i><i></i></div>

<!-- contact -->
<svg class="abs" style="left:0;top:4330px" width="1200" height="511" viewBox="0 0 1200 511">
  <path d="M0 215 C 400 140, 880 70, 1200 46 L1200 511 L0 511Z" fill="#0f2a4f"/>
  <path d="M1000 52 C 1080 28, 1140 14, 1200 8 L1200 40 C 1130 42, 1060 48, 1000 52Z" fill="#2196f3"/>
</svg>
<h2 class="abs contact-title">Contact Us <span>Today</span></h2>
<div class="abs c-item" style="top:4056px">
  <div class="ic"><svg width="22" height="22" viewBox="0 0 24 24"><path d="M5 3h4l2 5-2.5 1.5a11 11 0 0 0 6 6L16 13l5 2v4a2 2 0 0 1-2 2A16 16 0 0 1 3 5a2 2 0 0 1 2-2z" fill="none" stroke="#2196f3" stroke-width="1.4"/></svg></div>
  <div><div class="k">HEAD OFFICE</div><div class="v">21 Lorem Ipsum, ABC 123</div></div>
</div>
<div class="abs c-item" style="top:4128px">
  <div class="ic"><svg width="22" height="20" viewBox="0 0 24 20"><rect x="2" y="3" width="20" height="14" rx="1.5" fill="none" stroke="#2196f3" stroke-width="1.4"/><path d="M2 4l10 7 10-7" fill="none" stroke="#2196f3" stroke-width="1.4"/></svg></div>
  <div><div class="k">EMAIL ADDRESS</div><div class="v">name@company.com</div></div>
</div>
<div class="abs c-item" style="top:4196px">
  <div class="ic"></div>
  <div><div class="k">CALL US NOW</div><div class="v">Call Now: 123-456-789</div></div>
</div>

<div class="abs form">
  <h3>Send Us A Message</h3>
  <div class="lab" style="left:39px;top:116px">First Name</div>
  <div class="field" style="left:39px;top:133px;width:198px">John</div>
  <div class="lab" style="left:252px;top:116px">Last Name</div>
  <div class="field" style="left:252px;top:133px;width:198px">Doe</div>
  <div class="lab" style="left:39px;top:202px">Email</div>
  <div class="field" style="left:39px;top:221px;width:416px">Info@company.com</div>
  <div class="lab" style="left:39px;top:292px">Message</div>
  <div class="field area" style="left:39px;top:310px;width:416px">Type Your Message</div>
  <div class="btn">Contact us
    <svg width="18" height="14" viewBox="0 0 18 14"><path d="M1 7h15M11 2l5 5-5 5" stroke="#fff" stroke-width="1.6" fill="none"/></svg>
  </div>
</div>

<!-- footer -->
<div class="abs logo f-logo"><span class="dot"></span>Marlow Pool Service</div>
<div class="abs f-div" style="left:410px"></div>
<div class="abs f-info" style="left:432px">
  <svg width="28" height="28" viewBox="0 0 28 28"><circle cx="14" cy="14" r="12" fill="none" stroke="#fff" stroke-width="1.5"/><path d="M2 14h24M14 2c-5 7-5 17 0 24M14 2c5 7 5 17 0 24" fill="none" stroke="#fff" stroke-width="1.5"/></svg>
  <div>123, Building Name, Street<br>City, State XY 123456</div>
</div>
<div class="abs f-div" style="left:668px"></div>
<div class="abs f-info" style="left:689px">
  <svg width="26" height="30" viewBox="0 0 26 30"><rect x="3" y="2" width="14" height="26" rx="2" fill="none" stroke="#fff" stroke-width="1.5"/><path d="M20 11a5 5 0 0 1 0 8M23 8a9 9 0 0 1 0 14" fill="none" stroke="#fff" stroke-width="1.5"/></svg>
  <div>PHONE<br>(123) 456 7890</div>
</div>
<div class="abs f-div" style="left:843px"></div>
<div class="abs f-info" style="left:864px">
  <svg width="28" height="26" viewBox="0 0 28 26"><path d="M3 10l11-7 11 7v13H3z" fill="none" stroke="#fff" stroke-width="1.5"/><path d="M3 10l11 8 11-8" fill="none" stroke="#fff" stroke-width="1.5"/></svg>
  <div>EMAIL<br>info@company.com</div>
</div>
<div class="abs f-nav"><span>HOME</span><span>SERVICES</span><span>ABOUT US</span><span>TESTIMONIALS</span><span>BLOG</span><span>CONTACT US</span></div>
<div class="abs f-copy">Marlow Pool Service</div>
<div class="abs f-social" style="left:933px"><i></i></div>
<div class="abs f-social" style="left:966px"><i></i></div>
<div class="abs f-social" style="left:999px"><i></i></div>
<div class="abs f-social" style="left:1032px"><i></i></div>

</body>
</html>
```